Redesign of Form/Document Navigation Page

I need a redesign of our document and navigation bar on the left. We want the same navigation bar layout/setup but want the buttons and typography to be simple and matching all over. The form needs to be aesthetically pleasing and fit within the page.

1st attachment is our Direct Deposit and the second is the form continued.

```html
<!DOCTYPE html>
<html lang="en">
<head>
<meta charset="UTF-8">
<title>Employee Direct Deposit Enrollment Form</title>
<link href="https://fonts.googleapis.com/css2?family=Open+Sans:wght@300;400;600;700&display=swap" rel="stylesheet">
<style>
  :root{
    --navy:#1a1f71;
    --navy-dark:#141860;
    --bg:#e8e8e8;
    --white:#ffffff;
    --text:#333333;
    --muted:#555555;
    --line:#d6d6d6;
    --gold:#e9b31c;
    --green:#22a61f;
  }
  *{box-sizing:border-box;margin:0;padding:0}
  html,body{width:1160px;height:1200px;overflow:hidden}
  body{font-family:"Open Sans",sans-serif;color:var(--text);background:var(--bg);position:relative}
  .site-header{position:absolute;left:0;top:0;width:1160px;height:121px;background:var(--white);border-bottom:1px solid var(--line)}
  .brand{position:absolute;left:106px;top:44px;display:flex;align-items:center;gap:10px}
  .brand-mark{width:30px;height:30px;border-radius:50%;background:var(--navy)}
  .brand-name{font-size:20px;font-weight:700;color:var(--gold);line-height:1.05;text-transform:uppercase;letter-spacing:.3px}
  .main-nav{position:absolute;left:380px;top:51px;display:flex;gap:30px;font-size:12px;color:var(--muted)}
  .main-nav .active{color:var(--navy)}
  .user{position:absolute;right:106px;top:47px;display:flex;align-items:center;gap:14px;font-size:14px;color:#777}
  .power{width:24px;height:24px;border-radius:50%;background:var(--navy);display:flex;align-items:center;justify-content:center}
  .btn{background:var(--navy);color:var(--white);border-radius:3px;font-family:inherit;display:flex;align-items:center;justify-content:center}
  .back-btn{position:absolute;left:108px;top:153px;width:133px;height:32px;font-size:12px}
  .side-nav{position:absolute;left:108px;top:216px;width:218px;height:575px;background:var(--white);border:1px solid #dcdcdc;padding:29px 0 0 15px}
  .side-item{display:flex;align-items:center;gap:11px;height:47px;margin-bottom:28px;font-size:12px;color:#222}
  .side-icon{width:47px;height:47px;border-radius:50%;background:var(--navy);display:flex;align-items:center;justify-content:center;flex:none}
  .form-card{position:absolute;left:351px;top:216px;width:703px;height:842px;background:var(--white);border:1px solid #dcdcdc}
  .form-card > *{position:absolute}
  .form-title{left:0;right:0;top:40px;text-align:center;font-size:24px;font-weight:400;color:#333}
  .intro{left:23px;width:665px;font-size:10.5px;line-height:20px;color:var(--muted)}
  .attach-box{left:22px;top:229px;width:663px;height:95px;border:1px solid var(--line);text-align:center}
  .attach-link{display:block;margin-top:19px;font-size:10.5px;color:var(--navy);text-decoration:underline}
  .refresh-btn{width:75px;height:27px;margin:10px auto 0;font-size:10.5px}
  .section-title{left:27px;top:337px;font-size:15px;font-weight:600;color:#333}
  .note{left:27px;top:365px;font-size:10.5px;color:var(--muted)}
  .emphasis{left:26px;font-size:13.5px;font-weight:600;color:#333}
  .radio-row{display:flex;align-items:center;gap:0;font-size:11px;color:var(--muted)}
  .radio{width:13px;height:13px;border-radius:50%;border:1px solid #c8c8c8;margin-right:10px;flex:none}
  .radio-row .opt{display:flex;align-items:center;margin-right:12px}
  .field-label{font-size:13.5px;color:#444}
  .field-input{height:22px;border:1px solid #c9c9c9;background:var(--white)}
  .amount{display:flex;align-items:center;font-size:10.5px;color:var(--muted)}
  .amount-value{width:45px;height:22px;background:var(--green);color:var(--white);display:flex;align-items:center;padding-left:10px;margin:0 8px 0 14px}
  .legal{left:28px;top:722px;width:655px;font-size:10.5px;line-height:20px;color:var(--muted)}
  .site-footer{position:absolute;left:0;top:1110px;width:1160px;height:90px;background:var(--white);border-top:1px solid var(--line);text-align:center;font-size:10.5px;color:var(--muted);padding-top:37px}
</style>
</head>
<body>
  <header class="site-header">
    <div class="brand"><span class="brand-mark"></span><span class="brand-name">Northgate<br>Patrol Services</span></div>
    <nav class="main-nav"><span class="active">HOME</span><span>|</span><span>HELP</span></nav>
    <div class="user">Dana Ellis
      <span class="power"><svg width="12" height="12" viewBox="0 0 12 12" fill="none" stroke="#fff" stroke-width="1.6" stroke-linecap="round"><path d="M3.4 3.2a4 4 0 1 0 5.2 0"/><path d="M6 1.2v4.2"/></svg></span>
    </div>
  </header>

  <a class="btn back-btn">Back To Profile</a>

  <aside class="side-nav">
    <div class="side-item"><span class="side-icon"><svg width="22" height="22" viewBox="0 0 22 22" fill="none" stroke="#fff" stroke-width="1.4"><path d="M3 12l9-5 7 4-9 5z"/><path d="M3 14.5l7 4 9-5"/><path d="M3 17l7 4 9-5"/></svg></span>Direct Deposit</div>
    <div class="side-item"><span class="side-icon"><svg width="20" height="20" viewBox="0 0 20 20" fill="none" stroke="#fff" stroke-width="1.5"><rect x="3" y="4" width="11" height="13"/><path d="M6 8h5M6 11h5M6 14h3"/><path d="M12 12l6-8"/></svg></span>Change W-4</div>
    <div class="side-item"><span class="side-icon"><svg width="22" height="22" viewBox="0 0 22 22" fill="none" stroke="#fff" stroke-width="1.5"><circle cx="11" cy="11" r="9"/><circle cx="11" cy="11" r="5"/><circle cx="11" cy="11" r="1.5" fill="#fff"/></svg></span>Labour Code</div>
    <div class="side-item"><span class="side-icon"><svg width="20" height="20" viewBox="0 0 20 20" fill="#fff"><circle cx="10" cy="6" r="4"/><path d="M2 19c0-5 3.5-7 8-7s8 2 8 7z"/></svg></span>Personal Information</div>
    <div class="side-item"><span class="side-icon"><svg width="22" height="22" viewBox="0 0 24 24" fill="#fff"><path d="M12 2l3 6.5 7 .8-5.2 4.8 1.4 7L12 17.6 5.8 21l1.4-7L2 9.3l7-.8z"/></svg></span>Appraisal and Review</div>
    <div class="side-item"><span class="side-icon"><svg width="20" height="20" viewBox="0 0 20 20" fill="none" stroke="#fff" stroke-width="1.5"><path d="M4 16l1-4 9-9 3 3-9 9z"/><path d="M12 5l3 3"/></svg></span>Write Up-Slip</div>
    <div class="side-item"><span class="side-icon"><svg width="22" height="22" viewBox="0 0 22 22" fill="#fff"><rect x="3" y="15" width="2.5" height="5"/><rect x="7" y="13" width="2.5" height="7"/><rect x="11" y="11" width="2.5" height="9"/><rect x="15" y="8" width="2.5" height="12"/><path d="M3 12l6-4 3 2 5-6" fill="none" stroke="#fff" stroke-width="1.5"/><path d="M14 3h4v4z"/></svg></span>Employee Performance</div>
  </aside>

  <main class="form-card">
    <h1 class="form-title">Employee Direct Deposit Enrollment Form</h1>
    <p class="intro" style="top:93px">To enroll in Direct Deposit, simply fill out this form. Attach a voided check for each checking account - not a deposit slip. If depositing to a savings account, ask your bank to give you the Routing/Transit Number for your account. It isn't always the same as the number on a savings deposit slip. This will help ensure that you are paid correctly. Once filled out, accounting will review your information for processing. Once processed, you will receive an email confirmation with details.</p>
    <p class="intro" style="top:185px">Employees must attach a voided check for each of their accounts to help verify their account numbers and bank routing numbers.</p>

    <div class="attach-box">
      <a class="attach-link">Attach A Voided Check Or Bank Deposit Form for the Account</a>
      <div class="btn refresh-btn">Refresh</div>
    </div>

    <h2 class="section-title">Account Information</h2>
    <p class="note">The last item must be for the remaining amount owed to you. To distribute to more accounts, please complete another form.</p>
    <p class="emphasis" style="top:393px">Make sure to indicate what kind of account, along with enrolling or declining.</p>
    <p class="emphasis" style="top:424px;left:28px">**NOTIFY PAYROLL IMMEDIATELY IF YOU CLOSE OR CHANGE BANK ACCOUNT**</p>

    <div class="radio-row" style="left:28px;top:458px">
      <span class="opt"><span class="radio"></span>New Enrollment</span>
      <span class="opt"><span class="radio"></span>Change Enrollment</span>
      <span class="opt"><span class="radio"></span>Cancel Enrollment</span>
    </div>

    <label class="field-label" style="left:27px;top:503px">Bank Name:</label>
    <div class="field-input" style="left:27px;top:535px;width:203px"></div>
    <label class="field-label" style="left:275px;top:503px">City:</label>
    <div class="field-input" style="left:275px;top:535px;width:127px"></div>
    <label class="field-label" style="left:508px;top:503px">State:</label>
    <div class="field-input" style="left:508px;top:535px;width:174px"></div>

    <label class="field-label" style="left:27px;top:568px">Routing Transit #:</label>
    <div class="field-input" style="left:27px;top:599px;width:131px"></div>
    <label class="field-label" style="left:275px;top:568px">Account Number:</label>
    <div class="field-input" style="left:275px;top:599px;width:199px"></div>

    <div class="radio-row" style="left:28px;top:647px">
      <span class="opt"><span class="radio"></span>Checking</span>
      <span class="opt"><span class="radio"></span>Savings</span>
    </div>
    <div class="amount" style="left:388px;top:644px">Amount:<span class="amount-value">100</span>%</div>

    <p class="emphasis" style="top:692px">IMPORTANT! Please read and sign before completing and submitting.</p>
    <p class="legal">I hereby authorize NORTHGATE PATROL SERVICES to deposit any amounts owed me, as instructed by my employer, by initiating credit entries to my account at the financial institution (hereinafter "Bank") indicated on this form. Further, I authorize Bank to accept and to credit any credit entries indicated by NORTHGATE PATROL SERVICES to my account. In the event that NORTHGATE PATROL SERVICES deposits funds erroneously into my account, I authorize NORTHGATE PATROL SERVICES to</p>
  </main>

  <footer class="site-footer">Copyright © 2016 Northgate Patrol Services. All Right Reserved.</footer>
</body>
</html>
```